Stationery Set for Velmora Company

I need to create full stationery design for my company; Business Cards, Envelops, Letter Heads, Calendar.
In the letter head and Envelops... only contact information and website links.
Our company is a Service Management company with different domains of innovative services including Technology Service Management, Education Services, Outsourcing Management, Events Management.
I need a modern and innovative design specially for the business card. I some transparent designs and I like it, but don't limit your innovation to what I mentioned. Sky is limit for your innovation.

Target Market(s)

Middle East & Africa

Industry/Entity Type

Business Management

Colors
34a7d8
0355a3
85acd3
86cae7
cee9f5
cfdeed
e4daeb
f3f1f8
ecf7fb

Requirements
Must have
• Name, Title, Email, Mobile
Nice to have
• We have multiple locations in USA, KSA, EGY, so I need ideas about how to include all contact details maybe QR / Barcode or something else.
• Please see our locations and contact information: www.brightvelmora.example
Should not have
• Too much text

```html
<!DOCTYPE html>
<html lang="en">
<head>
<meta charset="utf-8">
<title>Velmora Company – Business Card</title>
<link href="https://fonts.googleapis.com/css2?family=Open+Sans:wght@400;600;700&display=swap" rel="stylesheet">
<style>
  :root{
    --bg:#ecebe8;
    --card:#ffffff;
    --ink:#3a3a3a;
    --brand:#0355a3;
    --panel:#3b6cb4;
    --strip:#d8d0da;
    --rule:#4a4a4a;
  }
  *{margin:0;padding:0;box-sizing:border-box}
  html,body{width:1200px;height:843px;overflow:hidden;background:var(--bg)}
  body{position:relative;font-family:"Open Sans",Arial,sans-serif;color:var(--ink)}

  .card{position:absolute;width:620px;height:354px;background:var(--card);
        box-shadow:0 6px 18px rgba(0,0,0,.18);overflow:hidden}
  .card--back{left:90px;top:60px}
  .card--front{left:490px;top:430px}

  .wordmark{display:flex;align-items:center;gap:12px}
  .wordmark__dot{width:18px;height:18px;border-radius:50%;background:var(--brand)}
  .wordmark__name{font-weight:700;font-size:52px;line-height:1;color:var(--brand);letter-spacing:1px}

  /* back */
  .card--back .wordmark{position:absolute;left:0;right:0;top:70px;justify-content:center}
  .address{position:absolute;left:56px;right:56px;top:190px;font-size:15px;line-height:1.55;color:var(--ink)}
  .address__rule{height:1px;background:var(--rule);margin-bottom:10px}
  .address__label{font-weight:700;color:var(--brand)}
  .address__line--indent{padding-left:40px}

  /* front */
  .card__strip{position:absolute;left:0;top:0;bottom:0;width:9px;background:var(--strip)}
  .card--front .wordmark{position:absolute;left:48px;top:128px}
  .card--front .wordmark__name{font-size:44px}
  .panel{position:absolute;left:330px;right:0;top:46px;bottom:46px;background:var(--panel);
         border-radius:20px 0 0 20px;padding:26px 20px 0 30px;color:#fff}
  .person__name{font-size:18px;font-weight:600;letter-spacing:1.5px;text-transform:uppercase}
  .person__title{font-size:14px;font-weight:600;letter-spacing:.5px;margin-top:2px;text-transform:uppercase}
  .contacts{list-style:none;margin-top:28px}
  .contacts li{display:flex;align-items:center;gap:9px;font-size:14px;line-height:21px;white-space:nowrap}
  .contacts svg{width:13px;height:13px;flex:none;fill:#fff}
</style>
</head>
<body>

<section class="card card--back" aria-label="Business card, back">
  <div class="wordmark">
    <span class="wordmark__dot"></span>
    <span class="wordmark__name">Velmora</span>
  </div>
  <div class="address">
    <div class="address__rule"></div>
    <div><span class="address__label">USA:</span> 410 Harbor Point Drive, Lakeview City, CA 90000 US</div>
    <div><span class="address__label">Saudi Arabia:</span> Riyadh, Al Malqa District, Al Noor St.</div>
    <div class="address__line--indent">Olaya Business Tower, P.O. Box 40215</div>
  </div>
</section>

<section class="card card--front" aria-label="Business card, front">
  <div class="card__strip"></div>
  <div class="wordmark">
    <span class="wordmark__dot"></span>
    <span class="wordmark__name">Velmora</span>
  </div>
  <div class="panel">
    <div class="person__name">Jonah Reyes</div>
    <div class="person__title">CEO/Founder</div>
    <ul class="contacts">
      <li><svg viewBox="0 0 16 16"><path d="M3.5 1l2.5 3-1.5 1.8c.8 1.9 2.2 3.4 4.2 4.3L10.5 8.6l3 2.4-1.6 2.9C7 13.6 2.4 9 2 4z"/></svg>+1.555 010 4477 (USA)</li>
      <li><svg viewBox="0 0 16 16"><path d="M3.5 1l2.5 3-1.5 1.8c.8 1.9 2.2 3.4 4.2 4.3L10.5 8.6l3 2.4-1.6 2.9C7 13.6 2.4 9 2 4z"/></svg>+966 9200 0123 (Saudi)</li>
      <li><svg viewBox="0 0 16 16"><path d="M4 0h8a1 1 0 0 1 1 1v14a1 1 0 0 1-1 1H4a1 1 0 0 1-1-1V1a1 1 0 0 1 1-1zm1 2v10h6V2zm3 11a1 1 0 1 0 0 2 1 1 0 0 0 0-2z"/></svg>+1.555 010 4477</li>
      <li><svg viewBox="0 0 16 16"><path d="M1 3h14v10H1zm1.5 1.2V12h11V4.2L8 8.6z M2.8 4 8 7.8 13.2 4z"/></svg>info@brightvelmora.example</li>
      <li><svg viewBox="0 0 16 16"><path d="M8 1a7 7 0 1 0 0 14A7 7 0 0 0 8 1zm0 1.5c.9 0 2 1.8 2.3 4.5H5.7C6 4.3 7.1 2.5 8 2.5zM2.6 8.5h2.9c.1 1.9.5 3.5 1.1 4.5A5.5 5.5 0 0 1 2.6 8.5zm0-1A5.5 5.5 0 0 1 6.6 3c-.6 1-1 2.6-1.1 4.5zm5.4 6c-.9 0-2-1.8-2.3-5h4.6c-.3 3.2-1.4 5-2.3 5zm1.4-.5c.6-1 1-2.6 1.1-4.5h2.9a5.5 5.5 0 0 1-4 4.5zm1.1-5.5c-.1-1.9-.5-3.5-1.1-4.5a5.5 5.5 0 0 1 4 4.5z"/></svg>www.brightvelmora.example</li>
    </ul>
  </div>
</section>

</body>
</html>
```